Business Card Design

We would like to re-design our business cards. Our Company - Qwinrel Turbochargers, rebuilds turbochargers and sells replacement parts. Our website is: http://www.qwinrelturbochargers-example.com
We just had our logo changed. I will attach the file. Looking for fresh new/modern business card. We like the colors red, black, white and silver. Black background looks attractive, but not a requirement. The final design should communicate reasonable/competitive prices, top quality and reliability of our products.
Updates
Project Deadline Extended
Reason: Need to finalize the info on the card. Currently working on changing address and email info. Want to make sure it is the correct one before accepting the final design. Unless, this is something that can be changed at a later time..??
Industry/Entity Type
Business
Contact Information for Business Card
QWINREL TURBOCHARGERS, LLC
20473 Harwick Lane NE
Massillon, OH 44647
Tel: +1-555-214-7390
Fax: +1-555-267-1842
info@QwinrelTurbochargers-example.com
Our current business card had the following highlights:
*We rebuild all Turbocharges for Automotive, Diesel and Industrial
*Precision Balancing and in-house turbocharger needs
*All Turbocharger replacement parts are made in USA / U.K.
Look and feel
Each slider illustrates characteristics of the customer's brand and the style your logo design should communicate.

```html
<!DOCTYPE html>
<html lang="en">
<head>
<meta charset="utf-8">
<title>Qwinrel Turbochargers – Business Card</title>
<link rel="stylesheet" href="https://fonts.googleapis.com/css2?family=Montserrat:wght@400;500;800&family=Open+Sans:wght@700&display=swap">
<style>
  :root {
    --bg: #d9d9d9;
    --card: #ffffff;
    --ink: #1c1c1c;
    --muted: #3a3a3a;
    --red: #e3241b;
    --band: #f3f3f3;
    --metal-a: #8a8a8a;
    --metal-b: #e6e6e6;
  }
  * { box-sizing: border-box; margin: 0; padding: 0; }
  html, body { width: 1200px; height: 852px; overflow: hidden; }
  body {
    background: var(--bg);
    font-family: "Montserrat", sans-serif;
    color: var(--ink);
    position: relative;
  }
  .card {
    position: absolute;
    width: 540px;
    height: 309px;
    background: var(--card);
    border-radius: 22px;
    box-shadow: 0 6px 14px rgba(0,0,0,.18);
    overflow: hidden;
  }
  .card--front { left: 40px; top: 272px; }
  .card--back { left: 620px; top: 272px; }

  .front-band { position: absolute; inset: 0; width: 100%; height: 100%; }
  .brand {
    position: absolute;
    display: flex; align-items: center; gap: 12px;
    font-family: "Montserrat", sans-serif;
    font-weight: 800;
    color: var(--ink);
    white-space: nowrap;
  }
  .brand__mark { border-radius: 50%; background: var(--red); flex: none; }
  .card--front .brand { left: 92px; top: 100px; font-size: 27px; }
  .card--front .brand__mark { width: 40px; height: 40px; }
  .front-url {
    position: absolute; left: 0; right: 0; top: 200px;
    text-align: center; font-size: 14px; color: var(--muted);
  }
  .rule { position: absolute; height: 2px; background: var(--red); }
  .rule--front-left { left: 24px; top: 262px; width: 120px; }
  .rule--front-right { left: 400px; top: 100px; width: 110px; }

  .card--back .brand { left: 150px; top: 30px; font-size: 23px; }
  .card--back .brand__mark { width: 34px; height: 34px; }
  .rule--back-top { left: 120px; top: 86px; width: 420px; }
  .part-photo {
    position: absolute; right: 22px; top: 104px;
    width: 150px; height: 82px; border-radius: 40px;
    background: linear-gradient(90deg, var(--metal-a), var(--metal-b));
  }
  .person { position: absolute; left: 34px; top: 140px; }
  .person__name {
    font-family: "Open Sans", sans-serif; font-weight: 700;
    color: var(--red); font-size: 17px; line-height: 22px;
  }
  .person__title { font-size: 12px; color: var(--muted); margin-top: 2px; }
  .rule--back-name { left: 206px; top: 154px; width: 140px; height: 1.5px; }
  .contact {
    position: absolute; left: 34px; top: 194px;
    font-size: 11.5px; color: var(--muted); line-height: 16px;
    list-style: none;
  }
  .contact li { display: flex; align-items: center; gap: 7px; }
  .contact__icon { width: 10px; height: 10px; fill: var(--red); flex: none; }
  .contact__address { margin-bottom: 4px; }
</style>
</head>
<body>
  <section class="card card--front">
    <svg class="front-band" viewBox="0 0 540 309" aria-hidden="true">
      <polygon points="300,0 360,0 250,309 190,309" fill="var(--band)"/>
      <polygon points="380,0 410,0 330,309 300,309" fill="var(--band)"/>
    </svg>
    <div class="brand"><span class="brand__mark"></span>Qwinrel Turbochargers</div>
    <p class="front-url">www.QwinrelTurbochargers-example.com</p>
    <div class="rule rule--front-left"></div>
    <div class="rule rule--front-right"></div>
  </section>

  <section class="card card--back">
    <div class="brand"><span class="brand__mark"></span>Qwinrel Turbochargers</div>
    <div class="rule rule--back-top"></div>
    <div class="part-photo" role="img" aria-label="Photo of a turbocharger shaft and compressor wheel"></div>
    <div class="person">
      <p class="person__name">Your Long Name</p>
      <p class="person__title">Title</p>
    </div>
    <div class="rule rule--back-name"></div>
    <ul class="contact">
      <li>4812 Corvale Ave. NW</li>
      <li class="contact__address">Brindle Falls, Ohio</li>
      <li><svg class="contact__icon" viewBox="0 0 10 10"><path d="M2 0h2l1 3-1.5 1a6 6 0 0 0 2.5 2.5L7 5l3 1v2a2 2 0 0 1-2 2A8 8 0 0 1 0 2a2 2 0 0 1 2-2z"/></svg>1.555.214.7390</li>
      <li><svg class="contact__icon" viewBox="0 0 10 10"><path d="M0 2h10v6H0z M0 2l5 3.5L10 2" stroke="#fff" stroke-width=".8"/></svg>info@QwinrelTurbochargers-example.com</li>
      <li><svg class="contact__icon" viewBox="0 0 10 10"><circle cx="5" cy="5" r="5"/><path d="M0 5h10M5 0v10" stroke="#fff" stroke-width=".8"/></svg>www.QwinrelTurbochargers-example.com</li>
    </ul>
  </section>
</body>
</html>
```